Im open to ideas.. I was thinking on my business cards aswell as my logo. a place for my name. email. phone number and abn..

ive attched a file with my business logo. which i dont love the colours.. i was think a dark background with charcoal letters so something along those colour schumes but im open to ideas..

BRM Constructions

```html
<!DOCTYPE html>
<html lang="en">
<head>
<meta charset="utf-8">
<title>BRM Constructions – Business Card</title>
<link rel="stylesheet" href="https://fonts.googleapis.com/css2?family=Source+Sans+3:wght@400;600;700&display=swap">
<style>
  :root {
    --bg: #ecebe8;
    --charcoal: #505052;
    --charcoal-deep: #454547;
    --paper: #ffffff;
    --mark-light: #c9c9cb;
    --ink-light: #e6e6e6;
    --ink-muted: #cfcfcf;
    --shadow: rgba(0, 0, 0, 0.18);
  }
  * { margin: 0; padding: 0; box-sizing: border-box; }
  html, body {
    width: 1200px; height: 900px; overflow: hidden;
    background: var(--bg);
    font-family: "Source Sans 3", "Myriad Pro", Arial, sans-serif;
  }
  .canvas {
    position: relative; width: 1200px; height: 900px;
    display: flex; align-items: center; justify-content: center; gap: 60px;
  }
  .card {
    position: relative; width: 520px; height: 318px;
    border-radius: 3px; overflow: hidden;
    box-shadow: 0 10px 28px var(--shadow);
  }

  /* Front */
  .card--front {
    background: var(--charcoal);
    display: flex; align-items: center; justify-content: center;
  }
  .brand {
    display: flex; align-items: center; gap: 12px;
    font-weight: 600; letter-spacing: 0.5px; white-space: nowrap;
  }
  .brand__dot { width: 14px; height: 14px; }
  .card--front .brand { font-size: 40px; color: var(--mark-light); }
  .card--front .brand__dot { background: var(--mark-light); }

  /* Back */
  .card--back { background: var(--paper); }
  .card--back .band-top {
    position: absolute; left: 0; top: 0; width: 100%; height: 170px;
    display: flex; align-items: center; justify-content: flex-end;
    padding-right: 48px;
  }
  .card--back .brand { font-size: 36px; color: var(--charcoal); }
  .card--back .brand__dot { background: var(--charcoal); }

  .band-bottom {
    position: absolute; left: 0; top: 170px; width: 100%; height: 148px;
    background: var(--charcoal-deep);
  }
  .contact {
    position: absolute; right: 24px; top: 14px;
    list-style: none; text-align: right;
    font-size: 13px; line-height: 18px; color: var(--ink-light);
  }
  .contact li { display: flex; align-items: center; justify-content: flex-end; gap: 8px; }
  .contact svg { width: 11px; height: 11px; fill: none; stroke: var(--ink-muted); stroke-width: 1.4; }

  .person { position: absolute; left: 40px; top: 58px; color: var(--ink-light); }
  .person__name { font-size: 19px; font-weight: 700; line-height: 22px; }
  .person__role { font-size: 15px; font-weight: 400; line-height: 20px; padding-left: 6px; color: var(--ink-muted); }
  .person__abn { margin-top: 12px; padding-left: 16px; font-size: 15px; line-height: 20px; }
  .person__abn b { font-weight: 700; }
</style>
</head>
<body>
  <main class="canvas">
    <section class="card card--front" aria-label="Business card front">
      <div class="brand"><span class="brand__dot"></span>BRM Constructions</div>
    </section>

    <section class="card card--back" aria-label="Business card back">
      <div class="band-top">
        <div class="brand"><span class="brand__dot"></span>BRM Constructions</div>
      </div>
      <div class="band-bottom">
        <ul class="contact">
          <li>(044) 123 456 789
            <svg viewBox="0 0 12 12"><path d="M2 1.5h2.5l1 2.5-1.5 1a6 6 0 0 0 3 3l1-1.5 2.5 1V10.5A1 1 0 0 1 9.5 11 8.5 8.5 0 0 1 1 2.5a1 1 0 0 1 1-1z"/></svg>
          </li>
          <li>info@youremail.com
            <svg viewBox="0 0 12 12"><rect x="1" y="2.5" width="10" height="7"/><path d="M1 2.5l5 4 5-4"/></svg>
          </li>
          <li>www.yourwebsite.com
            <svg viewBox="0 0 12 12"><circle cx="6" cy="6" r="5"/><path d="M1 6h10M6 1c-2.5 3-2.5 7 0 10M6 1c2.5 3 2.5 7 0 10"/></svg>
          </li>
        </ul>
        <div class="person">
          <p class="person__name">Daniel Hart</p>
          <p class="person__role">Managing Director</p>
          <p class="person__abn"><b>ABN:</b> 1234567</p>
        </div>
      </div>
    </section>
  </main>
</body>
</html>
```